Consulting company requires a logo and business card design

I require a logo/business card design for a new company based in Sexsmith Alberta called TallMarsh Integrity Consulting Ltd. I plan to provide the following services: Construction management/inspection for the oil and gas industry, as well as general consulting for Asset Management, fleet management, etc. Have attached a copy of resume for use as guide for

Target Market(s)

Businesses within the oil and gas production, construction and shipping industry

Industry/Entity Type

Oil And Gas

Contact Information for Business Card

Believe should highlight, services offered, safety, quality,

Logo Text

TallMarsh Integrity Consulting (TMIC) ?

Font styles to use
Script

Requirements
Must have
• Open to all options

```html
<!DOCTYPE html>
<html lang="en">
<head>
<meta charset="utf-8">
<title>TallMarsh Integrity Consulting – Business Card</title>
<link rel="stylesheet" href="https://fonts.googleapis.com/css2?family=Open+Sans:wght@400;600&display=swap">
<style>
  :root {
    --backdrop: #ecebe9;
    --card: #ffffff;
    --accent-red: #c9380f;
    --accent-orange: #e2561c;
    --text-grey: #444444;
    --text-dark: #2b2b2b;
    --brand-blue: #3b9ae6;
    --band-light: #5fdcf7;
    --band-deep: #3f86f2;
  }
  * { box-sizing: border-box; margin: 0; padding: 0; }
  html, body { width: 1200px; height: 900px; overflow: hidden; }
  body {
    background: var(--backdrop);
    font-family: "Open Sans", sans-serif;
    position: relative;
  }
  .card {
    position: absolute;
    background: var(--card);
    box-shadow: 0 4px 14px rgba(0,0,0,0.12);
    overflow: hidden;
  }
  .card-front { left: 238px; top: 62px; width: 555px; height: 343px; }
  .card-back  { left: 458px; top: 518px; width: 559px; height: 344px; }

  .holder-name {
    position: absolute; left: 40px; top: 33px;
    font-size: 22px; font-weight: 600; color: var(--accent-red);
  }
  .holder-title {
    position: absolute; left: 40px; top: 63px;
    font-size: 15px; color: var(--text-grey);
  }
  .address {
    position: absolute; left: 41px; top: 146px;
    font-size: 14.5px; line-height: 18px; color: var(--text-dark);
  }
  .contact-list {
    position: absolute; left: 44px; top: 199px;
    list-style: none; font-size: 14.5px; color: var(--text-dark);
  }
  .contact-list li { display: flex; align-items: center; height: 20px; }
  .contact-list svg { width: 10px; height: 10px; margin-right: 9px; fill: var(--accent-red); }

  .brand-band {
    position: absolute; right: 0; top: 0; width: 161px; height: 100%;
    background: linear-gradient(160deg, var(--band-light), var(--band-deep) 60%);
  }

  .brand-lockup {
    position: absolute; left: 0; right: 0; top: 82px;
    display: flex; align-items: center; justify-content: center; gap: 14px;
  }
  .brand-dot { width: 44px; height: 44px; border-radius: 50%; background: var(--brand-blue); }
  .brand-name {
    font-size: 28px; font-weight: 400; line-height: 34px; color: var(--brand-blue);
  }
  .services {
    position: absolute; left: 40px; right: 40px; top: 226px;
    text-align: center; font-size: 14.5px; line-height: 20px; color: var(--accent-orange);
  }
</style>
</head>
<body>
  <section class="card card-front">
    <h1 class="holder-name">Daniel Harlow</h1>
    <p class="holder-title">Managing Director</p>
    <p class="address">1234, Address Goes Here<br>Country Name, 123456</p>
    <ul class="contact-list">
      <li><svg viewBox="0 0 10 10"><rect x="2" y="0" width="6" height="10" rx="1"/></svg>123-456-7890</li>
      <li><svg viewBox="0 0 10 10"><path d="M0 3 Q5 0 10 3 L10 5 L7 5 L7 4 L3 4 L3 5 L0 5Z M1 6 H9 V10 H1Z"/></svg>123-456-7890</li>
      <li><svg viewBox="0 0 10 10"><rect x="0" y="3" width="10" height="7" rx="1"/><rect x="2" y="0" width="6" height="4"/></svg>123-456-7890</li>
      <li><svg viewBox="0 0 10 10"><path d="M0 2 H10 V9 H0Z M0 2 L5 6 L10 2" /></svg>info@tallmarsh-ic.com</li>
      <li><svg viewBox="0 0 10 10"><path d="M1 6 L4 3 L5 4 L2 7Z M5 3 L8 0 L10 2 L7 5 L6 4 L8 2Z M4 6 L5 7 L3 9 L1 10 L0 9 L2 7Z"/></svg>www.tallmarsh-ic.com</li>
    </ul>
    <div class="brand-band" role="img" aria-label="Brand emblem area in blue"></div>
  </section>

  <section class="card card-back">
    <div class="brand-lockup">
      <span class="brand-dot"></span>
      <p class="brand-name">TallMarsh Integrity<br>Consulting Ltd.</p>
    </div>
    <p class="services">We are a construction management/inspection for the oil and gas industry, as well as general consulting for Asset Management, fleet management.</p>
  </section>
</body>
</html>
```